sydney wedding photography business needs a business card design

we need a business card design for a sydney based wedding photography and videography business. our business name is :golden hour studio and film. our target clients are 24-35 yrs female. our style is candid, organic, natural, dynamic. we are a team of young photographers and videographers, and help brides to create memories that they will cherish for the rest of their lives. the logo will be provided. we want an elegant design that reflects our style, and also want to give a great impression to our clients that we are one of the best studios in sydney and our brand means quality and premium service.

Target Market(s)

bride to be, 24-35 years old, living in sydney and surrunding areas

Industry/Entity Type

Wedding Photography

Contact Information for Business Card

address: 57 tarrant street, glenmore nsw 2047
mobile: 0431872259
phone: (02) 9163 2408
info@tidewillowstudio.net.au
www.tidewillowstudio.net.au
facebook:tidewillowweddings
instagram:tidewillowweddings

Font styles to use
Serif
Sans Serif

Requirements
Nice to have
• maybe add my slogan"memories beyond eternity" if the layout looks good
Should not have
• no black color, not good idea for wedding biz card

```html
<!DOCTYPE html>
<html lang="en">
<head>
<meta charset="utf-8">
<title>Golden Hour Studio and Film – Business Card</title>
<link rel="stylesheet" href="https://fonts.googleapis.com/css2?family=Josefin+Sans:wght@300;400;600&display=swap">
<style>
  :root {
    --backdrop: #e9e5de;
    --card-white: #ffffff;
    --ink: #1a1a1a;
    --ink-soft: #3a3a3a;
    --gold: #c9961c;
    --gold-light: #e3ae17;
    --gold-deep: #9c6f12;
    --disc: #0e0e0e;
  }
  * { box-sizing: border-box; margin: 0; padding: 0; }
  html, body {
    width: 1200px; height: 950px; overflow: hidden;
    background: var(--backdrop);
    font-family: "Josefin Sans", Arial, sans-serif;
  }
  .stage {
    position: relative; width: 1200px; height: 950px;
  }
  .card {
    position: absolute; width: 540px; height: 309px;
    overflow: hidden;
    box-shadow: 0 10px 28px rgba(0,0,0,.18);
  }
  /* Front */
  .card-front { left: 30px; top: 320px; background: var(--card-white); }
  .front-disc { position: absolute; left: 0; top: 0; width: 540px; height: 309px; }
  .brand-name {
    position: absolute; left: 300px; top: 70px; width: 220px;
    text-align: center; color: var(--gold);
    font-weight: 600; font-size: 19px; letter-spacing: 1px; line-height: 1.3;
  }
  .person {
    position: absolute; left: 30px; top: 150px;
  }
  .person-name {
    color: var(--gold); font-weight: 400; font-size: 21px;
    letter-spacing: 1px; text-transform: uppercase;
  }
  .person-role {
    color: var(--ink); font-size: 14px; letter-spacing: 1px;
    text-transform: uppercase; margin-top: 2px;
  }
  .address {
    margin-top: 10px; color: var(--ink-soft); font-size: 13px;
    font-weight: 300; line-height: 1.3;
  }
  .contact-list {
    position: absolute; left: 140px; top: 200px; list-style: none;
  }
  .contact-item {
    display: flex; align-items: center; gap: 8px;
    color: var(--ink-soft); font-size: 12.5px; font-weight: 300;
    line-height: 15px;
  }
  .contact-icon { width: 11px; height: 11px; flex: none; }
  /* Back */
  .card-back {
    left: 630px; top: 320px;
    background: radial-gradient(ellipse at 55% 50%, var(--gold-light) 0%, var(--gold) 55%, var(--gold-deep) 100%);
  }
  .back-name {
    position: absolute; left: 0; right: 0; top: 132px;
    text-align: center; color: var(--disc);
    font-weight: 600; font-size: 22px; letter-spacing: 2px; text-transform: uppercase;
  }
  .back-web {
    position: absolute; left: 22px; top: 154px;
    transform: translate(-50%, -50%) rotate(90deg);
    transform-origin: center; white-space: nowrap;
    color: var(--disc); font-size: 12px; letter-spacing: 2px; font-weight: 400;
  }
</style>
</head>
<body>
<main class="stage">

  <section class="card card-front" aria-label="Business card front">
    <svg class="front-disc" viewBox="0 0 540 309" aria-hidden="true">
      <circle cx="410" cy="40" r="150" fill="var(--gold)"/>
      <circle cx="410" cy="30" r="150" fill="var(--disc)"/>
      <circle cx="410" cy="30" r="112" fill="none" stroke="#1d1d1d" stroke-width="26"/>
    </svg>
    <div class="brand-name">golden hour studio and film</div>

    <div class="person">
      <p class="person-name">Mara Ellison</p>
      <p class="person-role">Photographer</p>
      <p class="address">57 tarrant street<br>glenmore nsw 2047</p>
    </div>

    <ul class="contact-list">
      <li class="contact-item">
        <svg class="contact-icon" viewBox="0 0 12 12" aria-hidden="true"><path d="M2 1l2 0 1 3-1.3 1a7 7 0 0 0 3.3 3.3L8 7l3 1v2c0 .6-.5 1-1 1A9 9 0 0 1 1 2c0-.5.4-1 1-1z" fill="var(--gold)"/></svg>
        (02) 9163 2408
      </li>
      <li class="contact-item">
        <svg class="contact-icon" viewBox="0 0 12 12" aria-hidden="true"><rect x="3" y="0.5" width="6" height="11" rx="1" fill="none" stroke="var(--gold)" stroke-width="1.2"/></svg>
        (04) 3187 2259
      </li>
      <li class="contact-item">
        <svg class="contact-icon" viewBox="0 0 12 12" aria-hidden="true"><rect x="0.5" y="2" width="11" height="8" fill="none" stroke="var(--gold)" stroke-width="1.2"/><path d="M1 2.5l5 4 5-4" fill="none" stroke="var(--gold)" stroke-width="1.2"/></svg>
        info@tidewillowstudio.net.au
      </li>
      <li class="contact-item">
        <svg class="contact-icon" viewBox="0 0 12 12" aria-hidden="true"><circle cx="6" cy="6" r="5.2" fill="none" stroke="var(--gold)" stroke-width="1.2"/><path d="M1 6h10M6 1c2 2.5 2 7.5 0 10M6 1c-2 2.5-2 7.5 0 10" fill="none" stroke="var(--gold)" stroke-width="0.9"/></svg>
        tidewillowstudio.net.au
      </li>
      <li class="contact-item">
        <svg class="contact-icon" viewBox="0 0 12 12" aria-hidden="true"><rect x="1" y="1" width="10" height="10" fill="var(--gold)"/></svg>
        tidewillowweddings
      </li>
      <li class="contact-item">
        <svg class="contact-icon" viewBox="0 0 12 12" aria-hidden="true"><rect x="1" y="1" width="10" height="10" fill="var(--gold)"/></svg>
        tidewillowweddings
      </li>
    </ul>
  </section>

  <section class="card card-back" aria-label="Business card back">
    <p class="back-web">www.tidewillowstudio.net.au</p>
    <p class="back-name">golden hour studio and film</p>
  </section>

</main>
</body>
</html>
```